New career and executive coaching business needs a business card design including logo

Company name: 'Bramblefield Growth Partners.' The aim of my coaching engagements is to help people improve their communication in the workplace and achieve their career goals. The process involves working with individuals to help them uncover their strengths and talents, then leverage those to improve their working lives. The Tarwick Inventory is the starting point to the process. I am after an exciting and interesting business card design (including logo)which is professional yet will still get people's attention.

Industry/Entity Type

Business

Contact Information for Business Card

Name: Malcolm Dervaney
Position: Owner
Address: 58 Quorrin Ct, Elmbridge Vic 3190
Phone: 0418923047
Website: bramblefieldgrowth.com.au
Email: malcolm@bgp.com.au

Colors
33a6d7
00a990
0355a3
3176b5

Requirements
Must have
• logo

```html
<!DOCTYPE html>
<html lang="en">
<head>
<meta charset="utf-8">
<title>Bramblefield Growth Partners – Business Card</title>
<link href="https://fonts.googleapis.com/css2?family=Poppins:wght@600&family=Roboto:wght@400;500&display=swap" rel="stylesheet">
<style>
  :root {
    --backdrop: #000000;
    --card-stock: #e6e7e8;
    --deep-blue: #0355a3;
    --sky-blue: #33a6d7;
    --teal: #00a990;
    --mid-blue: #3176b5;
    --ink: #3a3a3c;
    --ink-soft: #4b4b4d;
    --faint-mark: #a9d6ea;
  }
  * { margin: 0; padding: 0; box-sizing: border-box; }
  html, body { width: 1200px; height: 900px; overflow: hidden; }
  body {
    background: var(--backdrop);
    font-family: "Roboto", Arial, sans-serif;
    position: relative;
  }
  .card {
    position: absolute;
    top: 295px;
    width: 540px;
    height: 310px;
    background: var(--card-stock);
    overflow: hidden;
  }
  .card--front { left: 40px; }
  .card--back { left: 620px; }

  .band {
    position: absolute;
    left: 0;
    width: 100%;
    height: 25px;
    display: flex;
  }
  .band--top { top: 0; }
  .band--bottom { bottom: 0; }
  .band__primary { width: 50%; background: var(--deep-blue); }
  .band__accent { width: 50%; background: var(--sky-blue); }

  /* Front */
  .brand {
    position: absolute;
    top: 62px;
    left: 0;
    width: 100%;
    display: flex;
    flex-direction: column;
    align-items: center;
  }
  .brand__dot {
    width: 110px;
    height: 110px;
    border-radius: 50%;
    background: var(--teal);
  }
  .brand__name {
    margin-top: 16px;
    font-family: "Poppins", Arial, sans-serif;
    font-weight: 600;
    font-size: 20px;
    color: var(--mid-blue);
  }
  .website {
    position: absolute;
    top: 252px;
    left: 0;
    width: 100%;
    text-align: center;
    font-size: 15px;
    letter-spacing: 3.2px;
    color: var(--ink);
  }

  /* Back */
  .holder {
    position: absolute;
    top: 58px;
    right: 26px;
    text-align: right;
  }
  .holder__name {
    font-family: "Poppins", Arial, sans-serif;
    font-weight: 600;
    font-size: 20px;
    line-height: 1.1;
    color: var(--mid-blue);
  }
  .holder__role {
    font-size: 12px;
    font-weight: 500;
    letter-spacing: 0.6px;
    color: var(--ink);
  }
  .contacts {
    position: absolute;
    top: 140px;
    left: 60px;
    list-style: none;
  }
  .contact {
    display: flex;
    align-items: center;
    height: 30px;
    margin-bottom: 13px;
  }
  .contact__icon {
    width: 28px;
    height: 28px;
    border-radius: 4px;
    background: var(--teal);
    display: flex;
    align-items: center;
    justify-content: center;
    margin-right: 22px;
  }
  .contact__text {
    font-size: 13px;
    color: var(--ink-soft);
  }
  .faint-mark {
    position: absolute;
    left: 367px;
    top: 118px;
    width: 130px;
    height: 130px;
    border-radius: 50%;
    background: var(--faint-mark);
    opacity: 0.8;
  }
</style>
</head>
<body>
  <section class="card card--front" aria-label="Card front">
    <div class="band band--top"><span class="band__primary"></span><span class="band__accent"></span></div>
    <div class="brand">
      <span class="brand__dot"></span>
      <span class="brand__name">Bramblefield Growth Partners</span>
    </div>
    <p class="website">bramblefieldgrowth.com.au</p>
    <div class="band band--bottom"><span class="band__primary"></span><span class="band__accent"></span></div>
  </section>

  <section class="card card--back" aria-label="Card back">
    <div class="band band--top"><span class="band__primary"></span><span class="band__accent"></span></div>
    <div class="holder">
      <p class="holder__name">Malcolm Dervaney</p>
      <p class="holder__role">OWNER</p>
    </div>
    <div class="faint-mark"></div>
    <ul class="contacts">
      <li class="contact">
        <span class="contact__icon">
          <svg width="16" height="16" viewBox="0 0 24 24" aria-hidden="true"><path fill="#fff" d="M6.6 10.8a15.2 15.2 0 0 0 6.6 6.6l2.2-2.2c.3-.3.7-.4 1-.2 1.1.4 2.3.6 3.6.6.6 0 1 .4 1 1V20c0 .6-.4 1-1 1A17 17 0 0 1 3 4c0-.6.4-1 1-1h3.5c.6 0 1 .4 1 1 0 1.3.2 2.5.6 3.6.1.3 0 .7-.2 1z"/></svg>
        </span>
        <span class="contact__text">0418923047</span>
      </li>
      <li class="contact">
        <span class="contact__icon">
          <svg width="16" height="16" viewBox="0 0 24 24" aria-hidden="true"><rect x="2" y="5" width="20" height="14" rx="1.5" fill="#fff"/><path d="M3 6l9 7 9-7" fill="none" stroke="#00a990" stroke-width="1.8"/></svg>
        </span>
        <span class="contact__text">malcolm@bgp.com.au</span>
      </li>
      <li class="contact">
        <span class="contact__icon">
          <svg width="16" height="16" viewBox="0 0 24 24" aria-hidden="true"><path fill="#fff" d="M12 2a7 7 0 0 0-7 7c0 5.2 7 13 7 13s7-7.8 7-13a7 7 0 0 0-7-7zm0 9.5A2.5 2.5 0 1 1 12 6.5a2.5 2.5 0 0 1 0 5z"/></svg>
        </span>
        <span class="contact__text">58 Quorrin Ct, Elmbridge Vic 3190</span>
      </li>
    </ul>
    <div class="band band--bottom"><span class="band__primary"></span><span class="band__accent"></span></div>
  </section>
</body>
</html>
```